Business Card Design

Looking for business card designs for a new business. there will be two cards of the same design (both lots of information below in contact info). We would like the logo diagonally across the card with the information split above and below the logo similar to sketch. happy to look at similar alternatives
Please use same colours as in logo design

Industry/Entity Type

Business

Contact Information for Business Card

Dwight Halloran
mob - 0491 738 204
ph - 02 6148 3920
fax - 02 6148 3975
email - dwight@kestrelbeams.com.au
14 Larkmoor Road, Taminda NSW 2340

Colin Marchetti
mob - 0438 912 557
ph - 02 6148 3920
fax - 02 6148 3975
email - colin@kestrelbeams.com.au

```html
<!DOCTYPE html>
<html lang="en">
<head>
<meta charset="utf-8">
<title>Kestrel Beams – Business Card</title>
<link rel="stylesheet" href="https://fonts.googleapis.com/css2?family=Source+Sans+3:wght@400;600;700&display=swap">
<style>
  :root {
    --teal: #0b7f7a;
    --teal-name: #1d6f73;
    --ink: #141414;
    --band: #dde6e7;
    --paper: #ffffff;
    --stage: #eef0f0;
    --card-edge: #2a2a2a;
  }
  * { box-sizing: border-box; margin: 0; padding: 0; }
  html, body {
    width: 1135px;
    height: 1200px;
    overflow: hidden;
  }
  body {
    position: relative;
    background: var(--stage);
    font-family: "Source Sans 3", Arial, sans-serif;
    color: var(--ink);
  }
  .card {
    position: absolute;
    width: 936px;
    height: 534px;
    overflow: hidden;
  }
  .card--front {
    left: 32px;
    top: 53px;
    background: var(--paper);
    border: 2px solid var(--card-edge);
  }
  .card--back {
    left: 157px;
    top: 620px;
    background: var(--teal);
  }
  .address-band {
    position: absolute;
    left: 0;
    right: 0;
    top: 444px;
    bottom: 0;
    background: var(--band);
  }
  .brand {
    position: absolute;
    left: 0;
    right: 0;
    display: flex;
    align-items: center;
    justify-content: center;
    gap: 22px;
    font-weight: 700;
    letter-spacing: -0.5px;
    line-height: 1;
  }
  .brand__mark {
    width: 54px;
    height: 54px;
    flex: none;
  }
  .card--front .brand { top: 120px; font-size: 76px; color: var(--ink); }
  .card--front .brand__mark { background: var(--teal); }
  .card--back .brand { top: 214px; font-size: 90px; color: var(--ink); }
  .card--back .brand__mark { width: 64px; height: 64px; background: var(--paper); }

  .person-name {
    position: absolute;
    left: 0; right: 0;
    top: 262px;
    text-align: center;
    font-size: 29px;
    font-weight: 700;
    color: var(--teal-name);
  }
  .contact-line {
    position: absolute;
    left: 0; right: 0;
    display: flex;
    justify-content: center;
    align-items: center;
    gap: 6px;
    font-size: 24px;
    color: var(--ink);
  }
  .contact-line--numbers { top: 342px; }
  .contact-line--email { top: 385px; }
  .contact-item { display: inline-flex; align-items: center; gap: 5px; }
  .contact-item + .contact-item { margin-left: 6px; }
  .icon { width: 20px; height: 20px; fill: var(--teal); flex: none; }
  .address {
    position: absolute;
    left: 0; right: 0;
    top: 472px;
    text-align: center;
    font-size: 24px;
    color: var(--ink);
  }
  .website {
    position: absolute;
    left: 0; right: 0;
    top: 424px;
    text-align: center;
    font-size: 29px;
    font-weight: 600;
    letter-spacing: 3px;
    color: var(--paper);
  }
</style>
</head>
<body>

<section class="card card--front" aria-label="Business card front">
  <div class="address-band"></div>

  <div class="brand">
    <span class="brand__mark"></span>
    <span class="brand__name">Kestrel Beams</span>
  </div>

  <p class="person-name">Colin Marchetti</p>

  <div class="contact-line contact-line--numbers">
    <span class="contact-item">
      <svg class="icon" viewBox="0 0 20 20" aria-label="Phone"><path d="M5 2c1 0 2.6 3.2 2.6 4 0 .9-1.6 1.4-1.6 2.3 0 1.6 3.9 5.6 5.5 5.6.9 0 1.4-1.6 2.3-1.6.8 0 4 1.6 4 2.6 0 2-2 3.4-3.7 3.4C8.5 18.3 1.7 11.5 1.7 5.7 1.7 4 3 2 5 2z"/></svg>
      02 6148 3920
    </span>
    <span class="contact-item">
      <svg class="icon" viewBox="0 0 20 20" aria-label="Mobile"><path d="M6 1h8a1.5 1.5 0 0 1 1.5 1.5v15A1.5 1.5 0 0 1 14 19H6a1.5 1.5 0 0 1-1.5-1.5v-15A1.5 1.5 0 0 1 6 1zm0.5 2.5v10h7v-10zM10 15.2a1.2 1.2 0 1 0 0 2.4 1.2 1.2 0 0 0 0-2.4z"/></svg>
      0438 912 557
    </span>
    <span class="contact-item">
      <svg class="icon" viewBox="0 0 20 20" aria-label="Fax"><path d="M5 3h8l2 2v4h2a2 2 0 0 1 2 2v5h-3v2H4v-2H1v-5a2 2 0 0 1 2-2h2zm2 2v4h6V6h-2V5zm-1 9v3h8v-3z"/></svg>
      02 6148 3975
    </span>
  </div>

  <div class="contact-line contact-line--email">
    <svg class="icon" viewBox="0 0 20 20" aria-label="Email"><path d="M2 5h16v11H2zm1.6 1.4L10 11l6.4-4.6z"/></svg>
    colin@kestrelbeams.com.au
  </div>

  <p class="address">14 Larkmoor Road, Corrabel NSW 2361</p>
</section>

<section class="card card--back" aria-label="Business card back">
  <div class="brand">
    <span class="brand__mark"></span>
    <span class="brand__name">Kestrel Beams</span>
  </div>
  <p class="website">www.kestrelbeams.com.au</p>
</section>

</body>
</html>
```